Garlic Farm for Farm Sales/Restaurant sales

Need a professional, but appealing to agriculture world. We are selling 27 kinds of Organic Garlic from a farm in Simla,CO. I have uploaded logo and business information-we are going to need a template, because I will need to use it for four separate people.
-We are trying to appeal to Farm to table restaurants
-As well as growers/farmers

Target Market(s)

Agriculture Sales/Restaurants-Organic

Industry/Entity Type

Agriculture

Contact Information for Business Card

Want it to look more unique then your average kelto stock card- I want it to look amazing

Font styles to use
Sans Serif

Colors
0455a3
ec1f27
fbed22
ffffff

Requirements
Must have
• Just be creative
Nice to have
• Colorful
Should not have
• plain

```html
<!DOCTYPE html>
<html lang="en">
<head>
<meta charset="utf-8">
<title>Prairie Crest Garlic – Business Card</title>
<link rel="stylesheet" href="https://fonts.googleapis.com/css2?family=Josefin+Sans:wght@400;600;700&display=swap">
<style>
  :root {
    --navy: #1b2f5e;
    --red: #d7232b;
    --yellow: #fbd800;
    --white: #ffffff;
    --stage: #2b2b2d;
    --ink-soft: #e8ecf5;
  }
  * { box-sizing: border-box; margin: 0; padding: 0; }
  html, body {
    width: 1200px; height: 900px; overflow: hidden;
    background: var(--stage);
    font-family: "Josefin Sans", sans-serif;
  }
  .canvas { position: relative; width: 1200px; height: 900px; }

  .card {
    position: absolute; width: 640px; height: 366px; overflow: hidden;
    box-shadow: 0 14px 30px rgba(0,0,0,.45);
  }

  /* Front */
  .card-front { left: 110px; top: 60px; background: var(--navy); }
  .front-brand {
    position: absolute; left: 330px; top: 70px;
    display: flex; flex-direction: column; align-items: flex-start; gap: 14px;
  }
  .brand-dot { width: 76px; height: 76px; border-radius: 50%; background: var(--red); border: 4px solid var(--white); }
  .brand-name {
    font-weight: 700; font-size: 30px; line-height: 1; letter-spacing: .5px;
    color: var(--white); white-space: nowrap;
  }
  .social-row { position: absolute; left: 390px; top: 240px; display: flex; gap: 22px; }
  .social-dot { width: 22px; height: 22px; border-radius: 50%; background: var(--white); }
  .front-stripe {
    position: absolute; left: 0; top: 300px; width: 340px; height: 22px;
    background: var(--yellow);
  }

  /* Back */
  .card-back { left: 450px; top: 474px; background: var(--white); }
  .back-band { position: absolute; inset: 0; }
  .back-brand {
    position: absolute; left: 40px; top: 70px; white-space: nowrap;
    font-weight: 700; font-size: 32px; line-height: 1; color: var(--navy);
  }
  .back-mark {
    position: absolute; right: 36px; top: 40px;
    width: 150px; height: 150px; border-radius: 50%;
    background: var(--red); border: 7px solid var(--white);
    box-shadow: 0 0 0 3px var(--red);
  }
  .contact {
    position: absolute; left: 40px; top: 196px; color: var(--white);
  }
  .contact-name {
    position: relative; font-weight: 700; font-size: 26px; letter-spacing: 1.5px;
    margin-bottom: 10px; white-space: nowrap;
  }
  .contact-name .surname { color: var(--red); }
  .contact-name::before {
    content: ""; position: absolute; left: -28px; top: 3px;
    width: 16px; height: 16px; background: var(--red);
  }
  .contact-address { font-size: 15px; margin-bottom: 14px; color: var(--ink-soft); white-space: nowrap; }
  .contact-list { list-style: none; position: relative; }
  .contact-list::before {
    content: ""; position: absolute; left: -22px; top: -6px;
    width: 4px; height: 100px; background: var(--yellow);
  }
  .contact-list li {
    display: flex; align-items: center; gap: 12px;
    font-size: 15px; margin-bottom: 8px; color: var(--ink-soft);
  }
  .contact-text { white-space: nowrap; }
  .icon {
    flex: none; width: 16px; height: 16px; background: var(--red);
    display: inline-flex; align-items: center; justify-content: center;
  }
  .icon svg { width: 11px; height: 11px; }
  .web-accent { color: var(--red); }
</style>
</head>
<body>
<main class="canvas">

  <section class="card card-front" aria-label="Card front">
    <div class="front-brand">
      <span class="brand-dot"></span>
      <span class="brand-name">Prairie Crest Garlic</span>
    </div>
    <div class="social-row" aria-label="Social links">
      <span class="social-dot"></span>
      <span class="social-dot"></span>
      <span class="social-dot"></span>
      <span class="social-dot"></span>
    </div>
    <div class="front-stripe"></div>
  </section>

  <section class="card card-back" aria-label="Card back">
    <svg class="back-band" viewBox="0 0 640 366" preserveAspectRatio="none" aria-hidden="true">
      <polygon points="22,170 640,90 640,300 22,340" fill="#1b2f5e"/>
    </svg>
    <div class="back-brand">Prairie Crest Garlic</div>
    <div class="back-mark"></div>

    <div class="contact">
      <p class="contact-name">DANA <span class="surname">MERCER</span></p>
      <p class="contact-address">P.O. Box 48 Larkin, CO 80912</p>
      <ul class="contact-list">
        <li><span class="icon"><svg viewBox="0 0 12 12"><path d="M2 1h3l1 3-2 1a7 7 0 0 0 3 3l1-2 3 1v3c-6 0-9-3-9-9z" fill="#fff"/></svg></span><span class="contact-text">719-555-0143</span></li>
        <li><span class="icon"><svg viewBox="0 0 12 12"><rect x="1" y="3" width="10" height="7" fill="none" stroke="#fff"/><path d="M1 3l5 4 5-4" fill="none" stroke="#fff"/></svg></span><span class="contact-text">Dana@PCGarlic.com</span></li>
        <li><span class="icon"><svg viewBox="0 0 12 12"><circle cx="6" cy="6" r="4.5" fill="none" stroke="#fff"/><path d="M1.5 6h9M6 1.5v9" stroke="#fff"/></svg></span><span class="contact-text">www.<span class="web-accent">PCG</span>arlic.com</span></li>
      </ul>
    </div>
  </section>

</main>
</body>
</html>
```